DJ Colm Vetter

I'm looking for a professional but still artsy/progressive design. I come from a hip hop/club DJ background playing a lot of underground music but have switched to doing more corporate parties and weddings recently. I am all about keeping the dancefloor moving and emotionally connecting with the crowd. I'd like a trendy/updated color palette. Something that's clean enough that looks professional but also trendy enough to convey that by the end of the night we'll be sweatily dancing to the latest hits. Some designers/artists I like: Tarn Olquist, Pavel Remy, Wendell Quarrie, Lumeno 7400, Silas Dravin.

```html
<!DOCTYPE html>
<html lang="en">
<head>
<meta charset="utf-8">
<title>DJ Colm Vetter – Business Card</title>
<link href="https://fonts.googleapis.com/css2?family=Arvo:wght@400;700&display=swap" rel="stylesheet">
<style>
  :root {
    --backdrop: #1b1b1b;
    --card: #232323;
    --card-sheen: #2c2c2c;
    --accent: #19a6e6;
    --ink: #f2f2f2;
  }
  html, body {
    margin: 0;
    padding: 0;
    width: 1200px;
    height: 900px;
    overflow: hidden;
    background: var(--backdrop);
    font-family: "Arvo", "Rockwell", serif;
  }
  .canvas {
    position: relative;
    width: 1200px;
    height: 900px;
    display: flex;
    flex-direction: column;
    align-items: center;
    justify-content: center;
    gap: 46px;
  }
  .card {
    position: relative;
    width: 660px;
    height: 377px;
    background: radial-gradient(ellipse at 80% 60%, var(--card-sheen), var(--card) 70%);
    box-shadow: 0 10px 30px rgba(0,0,0,0.55);
    box-sizing: border-box;
  }
  .card::after {
    content: "";
    position: absolute;
    left: 0;
    right: 0;
    bottom: 0;
    height: 4px;
    background: var(--accent);
  }
  .card-front {
    display: flex;
    align-items: center;
    justify-content: center;
  }
  .wordmark {
    margin: 0;
    color: var(--accent);
    font-weight: 400;
    text-transform: uppercase;
    letter-spacing: 0.5px;
    line-height: 1;
  }
  .card-front .wordmark {
    font-size: 44px;
    transform: translateY(-20px);
  }
  .card-back {
    display: flex;
    align-items: center;
    padding-left: 62px;
  }
  .card-back .wordmark {
    font-size: 32px;
    white-space: nowrap;
  }
  .divider {
    width: 2px;
    height: 78px;
    background: var(--accent);
    margin: 0 28px 0 26px;
  }
  .contact {
    list-style: none;
    margin: 0;
    padding: 0;
    color: var(--ink);
    font-size: 17px;
    line-height: 1.6;
  }
  .contact .label {
    color: var(--accent);
    display: inline-block;
    width: 16px;
  }
</style>
</head>
<body>
  <main class="canvas">
    <section class="card card-front">
      <h1 class="wordmark">DJ Colm Vetter</h1>
    </section>
    <section class="card card-back">
      <h2 class="wordmark">DJ Colm Vetter</h2>
      <div class="divider"></div>
      <ul class="contact">
        <li><span class="label">P</span> : +330 5184-2637</li>
        <li><span class="label">E</span> : info@DJColmVetter.com</li>
        <li><span class="label">W</span> : brightfloorsessions.com</li>
      </ul>
    </section>
  </main>
</body>
</html>
```